Heritage Hollow Business Cards

Require a business card design. <br/><br/>Needs to include logo (either round or long version) plus these details:<br/>Maya Torvell<br/>Heritage Hollow<br/>maya@kelvadtrading.com.au<br/>02 6481 7395<br/>PO Box Glenwarra NSW 2791<br/>www.heritagehollow.com.au<br/><br/>I need in an editable format so that I can create for multiple staff members. <br/><br/>

Target Market(s)

We are an online store selling renovation products to home owners are builders. Looking for a classic classy design.

Industry/Entity Type

Home And Garden

Contact Information for Business Card

Maya Torvell
Heritage Hollow
maya@kelvadtrading.com.au
02 6481 7395
PO Box Glenwarra NSW 2791
www.heritagehollow.com.au

Colors

Designer to choose colors to be used in the design.

Requirements
Must have
• Must include Logo.

```html
<!DOCTYPE html>
<html lang="en">
<head>
<meta charset="utf-8">
<title>Heritage Hollow Business Cards</title>
<link href="https://fonts.googleapis.com/css2?family=Work+Sans:wght@300;400;500;700&display=swap" rel="stylesheet">
<style>
  :root{
    --bg:#d8d8d8;
    --card-dark:#161616;
    --card-light:#ffffff;
    --ink:#111111;
    --ink-soft:#8a8a8a;
    --paper-text:#f2f2f2;
    --rule:#222222;
  }
  *{box-sizing:border-box;margin:0;padding:0}
  html,body{width:1200px;height:930px;overflow:hidden}
  body{background:var(--bg);font-family:"Work Sans",sans-serif;position:relative}
  .card{position:absolute;left:290px;width:620px;height:380px;border-radius:18px;box-shadow:0 8px 22px rgba(0,0,0,.18)}
  .card-front{top:55px;background:var(--card-dark);color:var(--paper-text)}
  .card-back{top:495px;background:var(--card-light);color:var(--ink)}

  .brand{display:flex;align-items:center;gap:14px;position:absolute}
  .brand-dot{width:26px;height:26px;border-radius:50%;border:1.5px solid currentColor}
  .brand-name{font-weight:500;font-size:30px;letter-spacing:.5px;white-space:nowrap}

  .card-front .brand{left:50%;top:120px;transform:translateX(-50%)}
  .front-url{position:absolute;left:0;right:0;bottom:62px;text-align:center;font-size:15px;letter-spacing:4px;font-weight:300}
  .front-url b{font-weight:500}

  .card-back .brand{right:40px;top:62px}
  .card-back .brand-name{font-size:24px}
  .back-rule{position:absolute;left:40px;right:40px;top:150px;height:1.5px;background:var(--rule)}
  .person{position:absolute;left:40px;top:205px}
  .person-name{font-weight:700;font-size:28px;letter-spacing:1px}
  .person-role{font-size:14px;color:var(--ink-soft);margin-top:2px}
  .person-rule{width:180px;height:1px;background:var(--rule);margin:12px 0 10px}
  .company{font-size:15px;font-weight:500}
  .address{font-size:15px;color:var(--ink-soft);line-height:1.35;margin-top:4px}
  .contacts{position:absolute;right:40px;top:180px;list-style:none}
  .contacts li{display:flex;align-items:center;gap:10px;font-size:15px;color:#444;line-height:1.7}
  .contacts svg{width:13px;height:13px;flex:none}
</style>
</head>
<body>
  <section class="card card-front">
    <div class="brand"><span class="brand-dot"></span><span class="brand-name">Heritage Hollow</span></div>
    <p class="front-url">www.<b>heritagehollow</b>.com.au</p>
  </section>

  <section class="card card-back">
    <div class="brand"><span class="brand-dot"></span><span class="brand-name">Heritage Hollow</span></div>
    <div class="back-rule"></div>
    <div class="person">
      <h1 class="person-name">Maya Torvell</h1>
      <p class="person-role">Director</p>
      <div class="person-rule"></div>
      <p class="company">Heritage Hollow</p>
      <p class="address">PO Box<br>Glenwarra NSW 2791</p>
    </div>
    <ul class="contacts">
      <li><svg viewBox="0 0 24 24"><path d="M6.6 10.8a15 15 0 0 0 6.6 6.6l2.2-2.2a1 1 0 0 1 1-.25 11.4 11.4 0 0 0 3.6.6 1 1 0 0 1 1 1V20a1 1 0 0 1-1 1A17 17 0 0 1 3 4a1 1 0 0 1 1-1h3.5a1 1 0 0 1 1 1c0 1.25.2 2.45.6 3.6a1 1 0 0 1-.25 1z" fill="#222"/></svg>02 6481 7395</li>
      <li><svg viewBox="0 0 24 24"><rect x="3" y="5" width="18" height="14" rx="1.5" fill="none" stroke="#222" stroke-width="2"/><path d="M3 6l9 7 9-7" fill="none" stroke="#222" stroke-width="2"/></svg>maya@kelvadtrading.com.au</li>
      <li><svg viewBox="0 0 24 24"><circle cx="12" cy="12" r="9" fill="none" stroke="#222" stroke-width="2"/><path d="M3 12h18M12 3c3 3 3 15 0 18M12 3c-3 3-3 15 0 18" fill="none" stroke="#222" stroke-width="1.6"/></svg>www.<b style="font-weight:500">heritagehollow</b>.com.au</li>
    </ul>
  </section>
</body>
</html>
```